Step and Repeat Backdrop for wedding reception photo booth

Would like to have a Step and Repeat Backdrop (8 foot high by 10 foot wide) that incorporates the wedding logo (attached) and the names Helen and Gavin. Background should be white, and wedding colors are burgundy and gold. Show me creativity :-) I have included some random samples.

```html
<!DOCTYPE html>
<html lang="en">
<head>
<meta charset="utf-8">
<title>Helen &amp; Gavin — Step and Repeat Backdrop</title>
<link rel="stylesheet" href="https://fonts.googleapis.com/css2?family=Playfair+Display:wght@500&display=swap">
<style>
  :root {
    --page-bg: #f2f1ee;
    --backdrop-white: #ffffff;
    --gold: #b8922f;
    --gold-band: #c29f38;
    --gold-soft: rgba(194, 159, 56, 0.55);
    --gold-fade: rgba(194, 159, 56, 0);
  }
  html, body {
    margin: 0;
    padding: 0;
    width: 1200px;
    height: 600px;
    overflow: hidden;
    background: var(--page-bg);
  }
  .canvas {
    position: relative;
    width: 1200px;
    height: 600px;
  }
  .backdrop {
    position: absolute;
    left: 240px;
    top: 12px;
    width: 720px;
    height: 576px;
    background: var(--backdrop-white);
    overflow: hidden;
  }
  .backdrop__band {
    position: absolute;
    left: 0;
    width: 100%;
    height: 21px;
    background: var(--gold-band);
  }
  .backdrop__band--top { top: 0; }
  .backdrop__band--bottom { bottom: 0; }

  .repeat-mark {
    position: absolute;
    transform: translate(-50%, -50%);
    font-family: "Playfair Display", serif;
    font-weight: 500;
    font-size: 30px;
    letter-spacing: -1px;
    line-height: 1;
    color: var(--gold);
    white-space: nowrap;
  }

  .centerpiece__ornament {
    position: absolute;
    left: 226px;
    width: 274px;
    height: 84px;
    border-radius: 50%;
    background: radial-gradient(ellipse at center, var(--gold-soft) 0%, var(--gold-fade) 72%);
  }
  .centerpiece__ornament--top { top: 149px; }
  .centerpiece__ornament--bottom { top: 346px; }

  .centerpiece__monogram {
    position: absolute;
    left: 363px;
    top: 291px;
    transform: translate(-50%, -50%);
    font-family: "Playfair Display", serif;
    font-weight: 500;
    font-size: 128px;
    letter-spacing: -6px;
    line-height: 1;
    color: var(--gold);
    white-space: nowrap;
  }
</style>
</head>
<body>
<main class="canvas">
  <section class="backdrop" aria-label="Helen and Gavin step and repeat backdrop">
    <div class="backdrop__band backdrop__band--top"></div>
    <div class="backdrop__band backdrop__band--bottom"></div>

    <!-- row 1 -->
    <span class="repeat-mark" style="left:146px; top:45px">H&amp;G</span>
    <span class="repeat-mark" style="left:363px; top:45px">H&amp;G</span>
    <span class="repeat-mark" style="left:580px; top:45px">H&amp;G</span>
    <!-- row 2 -->
    <span class="repeat-mark" style="left:39px; top:108px">H&amp;G</span>
    <span class="repeat-mark" style="left:255px; top:108px">H&amp;G</span>
    <span class="repeat-mark" style="left:472px; top:108px">H&amp;G</span>
    <span class="repeat-mark" style="left:689px; top:108px">H&amp;G</span>
    <!-- row 3 -->
    <span class="repeat-mark" style="left:146px; top:168px">H&amp;G</span>
    <span class="repeat-mark" style="left:580px; top:168px">H&amp;G</span>
    <!-- row 4 -->
    <span class="repeat-mark" style="left:39px; top:229px">H&amp;G</span>
    <span class="repeat-mark" style="left:689px; top:229px">H&amp;G</span>
    <!-- row 5 -->
    <span class="repeat-mark" style="left:146px; top:289px">H&amp;G</span>
    <span class="repeat-mark" style="left:580px; top:289px">H&amp;G</span>
    <!-- row 6 -->
    <span class="repeat-mark" style="left:39px; top:351px">H&amp;G</span>
    <span class="repeat-mark" style="left:689px; top:351px">H&amp;G</span>
    <!-- row 7 -->
    <span class="repeat-mark" style="left:146px; top:411px">H&amp;G</span>
    <span class="repeat-mark" style="left:580px; top:411px">H&amp;G</span>
    <!-- row 8 -->
    <span class="repeat-mark" style="left:39px; top:472px">H&amp;G</span>
    <span class="repeat-mark" style="left:255px; top:472px">H&amp;G</span>
    <span class="repeat-mark" style="left:472px; top:472px">H&amp;G</span>
    <span class="repeat-mark" style="left:689px; top:472px">H&amp;G</span>
    <!-- row 9 -->
    <span class="repeat-mark" style="left:146px; top:534px">H&amp;G</span>
    <span class="repeat-mark" style="left:363px; top:534px">H&amp;G</span>
    <span class="repeat-mark" style="left:580px; top:534px">H&amp;G</span>

    <div class="centerpiece">
      <div class="centerpiece__ornament centerpiece__ornament--top" role="img" aria-label="Gold scrollwork flourish with fleur-de-lis above the monogram"></div>
      <span class="centerpiece__monogram">H&amp;G</span>
      <div class="centerpiece__ornament centerpiece__ornament--bottom" role="img" aria-label="Gold scrollwork flourish with fleur-de-lis below the monogram"></div>
    </div>
  </section>
</main>
</body>
</html>
```